We need a new business card that reflects who we are. Professional, classy, modern, and service ori

We need a business card design for a window coverings design company in Kansas City called Bright Lane Interiors. We offer professional, modern, and high quality window covering products. We are looking to portray an image of a big, national franchise. We are a 5 location (with showrooms) business with 10 professional designers and 4 professional installers. These cards will be used with Thank you cards, given to realtors, and asked for referrals with.

Target Market(s)

Kansas City

Industry/Entity Type

Business

Contact Information for Business Card

We would like our card to look clean and simple on the front, featuring our logo and Marlow Fenwick's. Our designers' phone numbers and emails should be displayed as well as their title.

Font styles to use
Sans Serif

Colors

Designer to choose colors to be used in the design.

Requirements
Must have
• Front - Logos, name, phone number, email address
• Back - Showroom locations, social media? Appt date/time?
Nice to have
• I would like a clean and modern look (not contemporary. I like a white background, but I am open to ideas. Looking for a "National chain" look for a small business.
Should not have
• Too much busyness.

```html
<!DOCTYPE html>
<html lang="en">
<head>
<meta charset="utf-8">
<title>Bright Lane Interiors – Business Card</title>
<link rel="stylesheet" href="https://fonts.googleapis.com/css2?family=Roboto:wght@400;500&family=Roboto+Condensed:wght@400;700&display=swap">
<style>
  :root {
    --backdrop: #2b2b2b;
    --card: #f2f2f2;
    --red: #c8383e;
    --ink: #1b1b1b;
    --grey: #555;
    --partner-grey: #5f6468;
    --band-grey: #9a9a9a;
    --rule: #8a8a8a;
    --black: #0c0c0c;
    --white: #ffffff;
  }
  * { margin: 0; padding: 0; box-sizing: border-box; }
  html, body { width: 1200px; height: 960px; overflow: hidden; }
  body { background: var(--backdrop); position: relative; font-family: "Roboto", Arial, sans-serif; color: var(--ink); }

  .card { position: absolute; width: 600px; height: 342px; background: var(--card); box-shadow: 0 4px 10px rgba(0,0,0,.45); overflow: hidden; }
  .card--front { left: 322px; top: 108px; }
  .card--back { left: 320px; top: 493px; }

  /* Front */
  .brand { position: absolute; right: 28px; top: 96px; text-align: right; }
  .brand__mark { display: flex; align-items: center; justify-content: flex-end; gap: 10px; }
  .brand__square { width: 34px; height: 34px; background: var(--red); }
  .brand__name { font-family: "Roboto Condensed", sans-serif; font-weight: 700; font-size: 27px; color: var(--ink); letter-spacing: .3px; }
  .brand__tagline { margin-top: 10px; font-size: 12px; color: var(--ink); }

  .person { position: absolute; left: 28px; top: 202px; }
  .person__name { font-family: "Roboto Condensed", sans-serif; font-weight: 700; font-size: 24px; color: var(--red); line-height: 1; }
  .person__title { font-family: "Roboto", sans-serif; font-weight: 500; font-size: 15px; margin-top: 6px; }

  .rule { position: absolute; left: 28px; top: 257px; width: 530px; height: 1px; background: var(--rule); }

  .contact { position: absolute; left: 28px; top: 266px; list-style: none; font-size: 14px; color: #333; }
  .contact li { display: flex; align-items: center; gap: 8px; height: 20px; }
  .contact svg { width: 13px; height: 13px; fill: var(--red); }

  .front-band { position: absolute; left: 0; bottom: 0; width: 600px; height: 30px; }
  .website { position: absolute; right: 24px; bottom: 7px; color: var(--white); font-size: 14px; letter-spacing: .6px; }

  /* Back */
  .partner { position: absolute; top: 40px; width: 100%; text-align: center; font-family: "Roboto Condensed", sans-serif; font-weight: 700; font-size: 16px; color: var(--partner-grey); }

  .appointments { position: absolute; left: 82px; top: 80px; list-style: none; }
  .appointments li { display: flex; align-items: baseline; height: 45px; color: var(--red); }
  .appt__label { font-size: 17px; }
  .appt__dots { display: inline-block; border-bottom: 1px dotted #777; height: 1px; margin: 0 3px; }
  .appt__dots--date { width: 167px; }
  .appt__dots--time { width: 106px; }
  .appt__unit { font-size: 13px; }

  .showrooms { position: absolute; top: 258px; width: 100%; text-align: center; font-family: "Roboto Condensed", sans-serif; }
  .showrooms__title { font-weight: 700; font-size: 16px; color: var(--red); }
  .showrooms__list { font-size: 14px; color: var(--grey); margin-top: 4px; }
  .social { display: flex; justify-content: center; gap: 3px; margin-top: 8px; list-style: none; }
  .social li { width: 20px; height: 20px; border-radius: 50%; background: var(--red); }
</style>
</head>
<body>

<section class="card card--front">
  <div class="brand">
    <div class="brand__mark">
      <span class="brand__square"></span>
      <span class="brand__name">Bright Lane Interiors</span>
    </div>
    <p class="brand__tagline">Custom Window Coverings &amp; Interior Styling</p>
  </div>

  <div class="person">
    <h1 class="person__name">DANA WHITFIELD</h1>
    <p class="person__title">DESIGNER</p>
  </div>
  <div class="rule"></div>

  <ul class="contact">
    <li><svg viewBox="0 0 24 24"><path d="M6.6 10.8a15 15 0 0 0 6.6 6.6l2.2-2.2c.3-.3.7-.4 1-.2 1.1.4 2.3.6 3.6.6.6 0 1 .4 1 1V20c0 .6-.4 1-1 1A17 17 0 0 1 3 4c0-.6.4-1 1-1h3.5c.6 0 1 .4 1 1 0 1.3.2 2.5.6 3.6.1.3 0 .7-.2 1z"/></svg>913.555.0148</li>
    <li><svg viewBox="0 0 24 24"><path d="M2 5h20v14H2z"/><path d="M2 6l10 7 10-7" fill="none" stroke="#f2f2f2" stroke-width="1.8"/></svg>info@brightlaneinteriors.com</li>
  </ul>

  <svg class="front-band" viewBox="0 0 600 30" aria-hidden="true">
    <rect x="0" y="17" width="600" height="13" fill="var(--band-grey)"/>
    <polygon points="118,17 236,17 228,30 110,30" fill="var(--red)"/>
    <polygon points="350,0 600,0 600,30 328,30" fill="var(--white)"/>
    <polygon points="354,0 600,0 600,30 334,30" fill="var(--black)"/>
  </svg>
  <span class="website">www.brightlaneinteriors.com</span>
</section>

<section class="card card--back">
  <p class="partner">Marlow Fenwick Showroom</p>

  <ul class="appointments">
    <li><span class="appt__label">Date :</span><span class="appt__dots appt__dots--date"></span><span class="appt__label">Time :</span><span class="appt__dots appt__dots--time"></span><span class="appt__unit">AM/PM</span></li>
    <li><span class="appt__label">Date :</span><span class="appt__dots appt__dots--date"></span><span class="appt__label">Time :</span><span class="appt__dots appt__dots--time"></span><span class="appt__unit">AM/PM</span></li>
    <li><span class="appt__label">Date :</span><span class="appt__dots appt__dots--date"></span><span class="appt__label">Time :</span><span class="appt__dots appt__dots--time"></span><span class="appt__unit">AM/PM</span></li>
    <li><span class="appt__label">Date :</span><span class="appt__dots appt__dots--date"></span><span class="appt__label">Time :</span><span class="appt__dots appt__dots--time"></span><span class="appt__unit">AM/PM</span></li>
  </ul>

  <div class="showrooms">
    <h2 class="showrooms__title">SHOWROOM LOCATIONS</h2>
    <p class="showrooms__list">NORTHGATE | ELM RIDGE | CEDAR HILL | RIVERSIDE | OAK HOLLOW</p>
    <ul class="social" aria-label="Social media">
      <li></li><li></li><li></li><li></li>
    </ul>
  </div>
</section>

</body>
</html>
```